verdant terraces simple classy business card design

my name is colin barrow and I run a gardening business aimed at high class verdant terraces. the business name is verdant terraces and our logo was designed on pixel harbour .My clientel are anything from residential homes to businesses. I take pride in my work and know that I offer a service like no other in my area.
The business card will be used to represent my business and I want it to be not only rememberable, but simplistic and modern. Eye catching too. Of course I would like it relatable to gardening and appealing to the correct clientel - those being garden enthusiasts, prestigious homes and businesses that are after top of the line gardening services like no other on the market.
I am not a typical lawn mowing business so I don't want a typical card design that represents that. The gardens I work with are generally million dollar properties with owners who are very garden proud looking for upkeep and guidance from me along with sometimes whole new garden designs. I want the business cards to show to my clients that I take pride, as they do, in their garden. And I want them to know from my card that I am a professional, qualified horticulturist offering them a top of the line service for life. I want them to refer my business on. I want them to look at my business card and see class and professionalism in a modern unique bold way.
The card should be simple with the possibility of the logo on the front being embossed/debossed and my details on the back the card should have a organic garden feel it's very important to me that it is absolutely perfect
I am also very open to ideas and suggestions so look forward to seeing the designs. the business logo has been supplied with this project and I want the card to be double sided

Contact info is
Colin Barrow - Managing Director / Horticulturist
Phone : 0481 526 704
Email: colinbarrow@verdantterraces.example.au

Target Market(s)

high class gardens residential and commercial

Industry/Entity Type

Gardener

Contact Information for Business Card

Contact info is
Phone : 0481 526 704

PLEASE MAKE CARD DOUBLE SIDED

Requirements
Must have
• organic simple classy modern feel
• must flow with the current logo that has been supplied with this project
• Double sided
• Must explain in a simple way that I deal with high end gardens and I'm a qualified horticulturist
Nice to have
• embossed debossed logo
Should not have
• shouldn't be to busy or cheap looking

```html
<!DOCTYPE html>
<html lang="en">
<head>
<meta charset="utf-8">
<title>Verdant Terraces – Business Card</title>
<link rel="stylesheet" href="https://fonts.googleapis.com/css2?family=Arimo:wght@400;700&display=swap">
<style>
  :root {
    --backdrop: #8e908f;
    --paper: #f1f1f0;
    --leaf: #4c8a3f;
    --leaf-deep: #45803a;
    --leaf-faint: #e3e9e1;
    --ink: #2b2b2b;
    --ink-soft: #4a4a4a;
    --paper-on-green: #eef2ec;
  }
  * { margin: 0; padding: 0; box-sizing: border-box; }
  html, body {
    width: 1105px;
    height: 1200px;
    overflow: hidden;
    background: var(--backdrop);
    font-family: "Arimo", Arial, sans-serif;
  }
  .card {
    position: absolute;
    left: 182px;
    width: 747px;
    height: 427px;
    overflow: hidden;
  }
  .card--front { top: 119px; background: var(--paper); }
  .card--back { top: 635px; background: var(--leaf); }

  .faint-mark {
    position: absolute;
    left: 20px;
    top: 10px;
    width: 300px;
    height: 300px;
    border-radius: 50%;
    background: var(--leaf-faint);
  }

  .wordmark {
    position: absolute;
    text-align: center;
    font-weight: 700;
    text-transform: uppercase;
    line-height: 1;
  }
  .wordmark__dot {
    display: block;
    margin: 0 auto;
    border-radius: 50%;
  }
  .wordmark__main { display: block; letter-spacing: 0.02em; }
  .wordmark__sub { display: block; }

  .card--front .wordmark { left: 388px; width: 318px; top: 26px; color: var(--leaf); }
  .card--front .wordmark__dot { width: 80px; height: 80px; background: var(--leaf); margin-bottom: 14px; }
  .card--front .wordmark__main { font-size: 33px; }
  .card--front .wordmark__sub { font-size: 19px; letter-spacing: 0.62em; margin-top: 7px; padding-left: 0.62em; }

  .card--back .wordmark { left: 0; width: 100%; top: 117px; color: var(--paper-on-green); }
  .card--back .wordmark__dot { width: 92px; height: 92px; background: var(--paper-on-green); margin-bottom: 16px; }
  .card--back .wordmark__main { font-size: 36px; }
  .card--back .wordmark__sub { font-size: 21px; letter-spacing: 0.7em; margin-top: 9px; padding-left: 0.7em; }

  .accent-bar {
    position: absolute;
    left: 0;
    top: 233px;
    width: 11px;
    height: 56px;
    background: var(--leaf);
  }
  .person { position: absolute; left: 39px; top: 232px; }
  .person__name { font-size: 25px; font-weight: 700; color: var(--leaf); line-height: 1.1; }
  .person__role { font-size: 19px; color: var(--ink); margin-top: 6px; }

  .divider {
    position: absolute;
    left: 39px;
    top: 305px;
    width: 659px;
    height: 2px;
    background: var(--leaf);
  }
  .contacts { position: absolute; left: 48px; top: 316px; list-style: none; }
  .contacts__item {
    display: flex;
    align-items: center;
    height: 28.5px;
    font-size: 18px;
    color: var(--ink-soft);
  }
  .contacts__icon { width: 16px; height: 16px; margin-right: 9px; fill: var(--leaf); flex: none; }
</style>
</head>
<body>

<section class="card card--front" aria-label="Card front">
  <div class="faint-mark" aria-hidden="true"></div>

  <div class="wordmark">
    <span class="wordmark__dot" aria-hidden="true"></span>
    <span class="wordmark__main">Verdant</span>
    <span class="wordmark__sub">Terraces</span>
  </div>

  <div class="accent-bar"></div>
  <div class="person">
    <p class="person__name">Colin Barrow</p>
    <p class="person__role">Managing Director / Horticulturist</p>
  </div>

  <div class="divider"></div>

  <ul class="contacts">
    <li class="contacts__item">
      <svg class="contacts__icon" viewBox="0 0 16 16" aria-hidden="true">
        <path d="M1 5c0-2 3-3 7-3s7 1 7 3v1h-4V5H5v1H1z"/>
        <path d="M3 8h10l1 6H2z"/>
      </svg>
      0481 526 704
    </li>
    <li class="contacts__item">
      <svg class="contacts__icon" viewBox="0 0 16 16" aria-hidden="true">
        <path d="M1 3h14v1.5L8 9 1 4.5z"/>
        <path d="M1 6.3l7 4.5 7-4.5V13H1z"/>
      </svg>
      colinbarrow@verdantterraces.example.au
    </li>
    <li class="contacts__item">
      <svg class="contacts__icon" viewBox="0 0 16 16" aria-hidden="true">
        <circle cx="8" cy="8" r="7.5"/>
        <path d="M4 5h3v3H5zM9 9h3v2l-2 2H9z" fill="#f1f1f0"/>
      </svg>
      verdantterraces.example.au
    </li>
  </ul>
</section>

<section class="card card--back" aria-label="Card back">
  <div class="wordmark">
    <span class="wordmark__dot" aria-hidden="true"></span>
    <span class="wordmark__main">Verdant</span>
    <span class="wordmark__sub">Terraces</span>
  </div>
</section>

</body>
</html>
```